A website where experts collaborate on your project

I am building a new website where experts (yes, like designers) collaborate on projects with the project owner. More minds = more collaboration = better end product. Please see Pelmora(dot)com for a quick landing page I created for collaborating on presentations (although there will be many project types offered)

I am looking for a DESIGNER LONG TERM, but for now, just need initial mock ups to show the web programmers.

I have 21 Word documents loosely designed, what I would like to see here is a theme. Please DO NOT GO OFF WHAT YOU CURRENTLY SEE AT PELMORA. What is up now is only a quick landing page.

You can view a Word doc of the homepage here:
https://www.filevanta.com/s/qx83kdm2/home.docx?dl=0

WHAT AM I LOOKING FOR?
A clean, well designed theme.

Here is a link to the logo:
https://www.filevanta.com/s/mr47tpz9/logo%20-%20horizontal.tif?dl=0
-----------------------------------------
Here are a few sites I like the design of and what I like about them:
www.quenbrook.com-all around my favorite, beautiful graphics, clean layout, bold use of colors on a dark background
Ravelto.com- clean layout, The use of humans and bubble style elements.
Mintharbor.com :) clean, bold, unique pop art style but professional
plumevault.com - From the unique colors and artwork and the ability of that art to not interfere with the important elements of the site
sparkwidgets.com-clean, nice colors, well organized and separated sections.
www.dunmereco.com-love the font, use of colors and sectionalized style

All in all, I am not picky and open to so many styles. I would ultimately like the designer I pick to design all 21 pages.
Updates

Hello everyone,Moving forward, I would like you all to pay special attention to the section in my brief titled "Here are a few sites I like the design of and what I like about them". Please see below, I handpicked each one of these as sites I really like. Thank you.Here are a few sites I like the design of and what I like about them:Ravelto.com- clean layout, The use of humans and bubble style elements.Mintharbor.com :) clean, bold, unique pop art style but professionalwriteraccess.com - From the unique colors and artwork and the ability of that art to not interfere with the important elements of the sitegrowthgeeks.com-clean, nice colors, well organized and separated sections.www.dunmereco.com-love the font, use of colors and sectionalized stylewww.quenbrook.com-beautiful graphics, clean layout, bold use of colors----------------------------------------- Added Tuesday, November 24, 2015

I updated the homepage, you can see it here:https://www.dropbox.com/s/kwlkbsookq3cg2m/1new%20homepage.docx?dl=0I am modeling it after my favorite designed site: triplelift.comI love the dark colors with the orange glowing style boldness of the buttons. It's real clean too. Added Tuesday, November 24, 2015

Target Market(s)

small business owners, marketers, freelancer writers, graphic designers,

Industry/Entity Type

Building

Number of Pages Required

5+ page

Requirements
Must have
• I can't think of anything the project must have.
Nice to have
• WHAT AM I LOOKING FOR?
• A clean, well designed theme. I had a designer do a bit of work putting elements together, I found it to be very plain, but I like the Application Page (https://www.filevanta.com/s/jb19ckr3/Pelmora-Website.ai?dl=0)
• Here is a link to the logo:
• https://www.filevanta.com/s/mr47tpz9/logo%20-%20horizontal.tif?dl=0
• Here are a few sites I like the design of and what I like about them:
• Ravelto.com- clean layout, The use of humans and bubble style elements.
• Mintharbor.com :) clean, bold, unique pop art style but professional
• plumevault.com - From the unique colors and artwork and the ability of that art to not interfere with the important elements of the site
• sparkwidgets.com-clean, nice colors, well organized and separated sections.
• www.dunmereco.com-love the font, use of colors and sectionalized style
• www.quenbrook.com-beautiful graphics, clean layout, bold use of colors
• -----------------------------------------
Should not have
• out of the boxed, templated style website. I want this site to be memorable and not look like a thousand others

```html
<!DOCTYPE html>
<html lang="en">
<head>
<meta charset="utf-8">
<title>Pelmora – Experts collaborating on your project</title>
<link href="https://fonts.googleapis.com/css2?family=Open+Sans:wght@400;600;700;800&display=swap" rel="stylesheet">
<style>
:root{
  --blue:#3fa9cf;
  --blue-dark:#2d8fb4;
  --blue-deep:#1f7699;
  --orange:#f7931e;
  --orange-dark:#ef7a12;
  --ink:#4a4f55;
  --muted:#8a9097;
  --line:#e3e6ea;
  --page:#eef1f4;
  --white:#ffffff;
  --footer:#3aa6cc;
}
*{box-sizing:border-box;margin:0;padding:0}
html,body{width:1200px;height:2260px;overflow:hidden}
body{font-family:'Open Sans',Arial,sans-serif;color:var(--ink);background:var(--page);position:relative}

/* header */
.site-header{position:absolute;left:0;top:0;width:1200px;height:140px;background:var(--white)}
.notice{position:absolute;left:480px;top:0;width:440px;height:66px;background:var(--orange);color:var(--white);font-size:11px;line-height:16px;padding:10px 18px}
.search{position:absolute;left:160px;top:86px;width:240px;height:32px;border:1px solid var(--line);display:flex}
.search span{flex:1;font-size:11px;color:var(--muted);padding:8px 10px}
.search i{width:32px;background:var(--blue);display:flex;align-items:center;justify-content:center}
.main-nav{position:absolute;left:416px;top:94px;display:flex;gap:24px;font-size:11px;font-weight:700;color:var(--ink)}
.brand{position:absolute;left:940px;top:84px;width:200px;text-align:right}
.brand-name{font-size:26px;font-weight:700;color:var(--blue-dark);line-height:32px}

/* hero */
.hero{position:absolute;left:0;top:140px;width:1200px;height:540px;overflow:hidden}
.hero-bg{position:absolute;inset:0;background:linear-gradient(100deg,#3aa3cb 0%,#5bb8d8 40%,#9fcfe0 62%,#d9e4ea 100%)}
.hero-photo{position:absolute;left:560px;top:0;width:640px;height:540px;background:linear-gradient(180deg,#c9d8e0 0%,#e6ecef 55%,#b9c6cd 100%);opacity:.9}
.hero-copy{position:absolute;left:160px;top:96px;color:var(--white)}
.hero-copy h1{font-size:30px;font-weight:700;line-height:38px;letter-spacing:.5px}
.hero-copy h1 strong{display:block;font-size:44px;font-weight:800;line-height:52px}
.hero-copy p{font-size:19px;line-height:27px;margin-top:18px;width:340px}
.btn{display:inline-block;background:var(--orange);color:var(--white);font-weight:700;font-size:14px;padding:13px 26px;border-radius:3px;margin-top:26px}
.hero-curve{position:absolute;left:0;bottom:0}

/* filters */
.filters{position:absolute;left:152px;top:690px;width:190px;height:570px;background:var(--white);box-shadow:0 1px 3px rgba(0,0,0,.08)}
.filters-head{height:36px;background:var(--orange);color:var(--white);font-size:12px;font-weight:700;padding:10px 14px}
.filters-body{padding:14px;font-size:10px;color:var(--muted)}
.filters-body h4{font-size:10px;color:var(--ink);font-weight:700;margin:4px 0 8px}
.check{display:flex;align-items:center;gap:6px;margin-bottom:9px}
.check b{width:9px;height:9px;border:1px solid #bcc2c8;display:block}
.slider{height:4px;background:var(--line);position:relative;margin:16px 0 8px}
.slider span{position:absolute;left:15%;right:20%;top:0;bottom:0;background:var(--blue)}
.range{display:flex;justify-content:space-between;margin-bottom:28px}
.apply{display:inline-block;background:var(--blue);color:var(--white);font-size:9px;font-weight:700;padding:7px 12px;margin-top:16px}

/* projects */
.projects{position:absolute;left:372px;top:690px;width:676px;height:1030px;background:var(--white);box-shadow:0 1px 3px rgba(0,0,0,.08)}
.projects-head{height:40px;background:var(--blue);color:var(--white);display:flex;justify-content:space-between;align-items:center;padding:0 16px}
.projects-head h2{font-size:13px;font-weight:700}
.projects-head small{font-size:9px}
.project{display:flex;gap:20px;padding:22px 20px;height:196px;border-bottom:1px solid var(--line)}
.project:last-child{border-bottom:none}
.thumb{width:170px;height:150px;flex:none}
.project h3{font-size:17px;font-weight:600;color:var(--orange);line-height:22px}
.meta{display:flex;gap:18px;align-items:center;font-size:10px;color:var(--muted);margin:10px 0}
.meta strong{font-size:13px;color:var(--ink)}
.bar{width:40px;height:5px;background:var(--line);position:relative}
.bar span{position:absolute;left:0;top:0;bottom:0;width:60%;background:var(--orange)}
.project p{font-size:11px;line-height:17px;color:var(--muted)}
.more{font-size:10px;color:var(--blue);font-weight:700;margin-top:8px}

/* testimonials */
.testimonials{position:absolute;left:0;top:1700px;width:1200px;height:410px}
.testimonials svg{position:absolute;left:0;top:0}
.testi-copy{position:absolute;left:200px;top:98px;width:800px;text-align:center;color:var(--white)}
.testi-copy h2{font-size:17px;font-weight:700;letter-spacing:.5px}
.testi-copy p{font-size:13px;line-height:21px;margin-top:18px}
.avatar{width:62px;height:62px;border-radius:50%;background:linear-gradient(#e7c9a9,#a8826a);border:3px solid var(--white);margin:18px auto 6px}
.testi-copy .name{font-size:11px;font-weight:700;margin-top:0}
.testi-copy .role{font-size:10px;margin-top:0;line-height:14px}
.arrow{position:absolute;top:250px;color:var(--white);font-size:36px;font-weight:300}

/* clients */
.clients{position:absolute;left:0;top:2110px;width:1200px;height:70px;background:var(--white);display:flex;justify-content:center;align-items:center;gap:70px}
.client{display:flex;align-items:center;gap:8px;font-size:20px;font-weight:600;color:#6f757b}
.client i{width:22px;height:22px;border-radius:50%;background:#6f757b;display:block}

/* footer */
.site-footer{position:absolute;left:0;top:2180px;width:1200px;height:80px;background:var(--footer);color:var(--white)}
.foot-nav{position:absolute;left:160px;top:24px;display:flex;gap:24px;font-size:10px;font-weight:700}
.copyright{position:absolute;left:160px;top:48px;font-size:9px;opacity:.85}
.social{position:absolute;left:900px;top:20px;display:flex;gap:10px}
.social i{width:30px;height:30px;border-radius:50%;border:2px solid var(--white);display:block}
</style>
</head>
<body>

<header class="site-header">
  <div class="notice">Welcome to our new platform. Post a project and let experts collaborate with you today.</div>
  <div class="search"><span>Choose Categories</span><i><svg width="12" height="12" viewBox="0 0 12 12"><circle cx="5" cy="5" r="3.5" fill="none" stroke="#fff" stroke-width="1.5"/><line x1="7.5" y1="7.5" x2="11" y2="11" stroke="#fff" stroke-width="1.5"/></svg></i></div>
  <nav class="main-nav"><span>HOME</span><span>PROJECTS</span><span>HOW IT WORKS</span><span>PRICING</span><span>MY ACCOUNT</span></nav>
  <div class="brand"><span class="brand-name">Pelmora</span></div>
</header>

<section class="hero">
  <div class="hero-bg"></div>
  <div class="hero-photo" role="img" aria-label="Photo of a businessman working at a laptop in a bright office"></div>
  <div class="hero-copy">
    <h1>CONVERT MORE <strong>CUSTOMERS</strong></h1>
    <p>Experience the power of experts collaborating on your project.</p>
    <span class="btn">GET STARTED &#9656;</span>
  </div>
  <svg class="hero-curve" width="1200" height="90" viewBox="0 0 1200 90"><path d="M0 90 L0 40 C300 95 700 95 1200 10 L1200 90 Z" fill="#eef1f4"/></svg>
</section>

<aside class="filters">
  <div class="filters-head">&#9776; FILTERS</div>
  <div class="filters-body">
    <h4>PRICE</h4>
    <div class="check"><b></b>$100 to $250</div>
    <div class="check"><b></b>$250 to $500</div>
    <div class="check"><b></b>$500 to $750</div>
    <div class="check"><b></b>$750 to $1000</div>
    <div class="check"><b></b>$1000 and above</div>
    <div class="slider"><span></span></div>
    <div class="range"><span>$0</span><span>$2000</span></div>
    <div class="check"><b></b>Country</div>
    <div class="check"><b></b>Categories</div>
    <div class="check"><b></b>Time Left</div>
    <div class="check"><b></b>Number of Experts</div>
    <div class="check"><b></b>Project Status</div>
    <div class="check"><b></b>Reviews</div>
    <div class="check"><b></b>Skill Level</div>
    <span class="apply">SEARCH NOW</span>
  </div>
</aside>

<main class="projects">
  <div class="projects-head"><h2>CROWD PROJECTS</h2><small>SORT BY: Newest &middot; Budget &middot; Ending</small></div>

  <article class="project">
    <div class="thumb" role="img" aria-label="Photo of a person working at a desk" style="background:linear-gradient(135deg,#9fb4c2,#d7dde1)"></div>
    <div>
      <h3>Morbi in ante arcu. Maecenas sit amet sem vel</h3>
      <div class="meta"><strong>$85</strong><div class="bar"><span></span></div><span>&#9201; Time left: 4 days</span></div>
      <p>Neque porro quisquam est qui dolorem ipsum quia dolor sit amet, consectetur adipisci velit, sed quia non numquam eius modi tempora incidunt ut labore et dolore magnam aliquam quaerat voluptatem.</p>
      <div class="more">READ MORE &rsaquo;</div>
    </div>
  </article>

  <article class="project">
    <div class="thumb" role="img" aria-label="Photo of two colleagues reviewing a document" style="background:linear-gradient(135deg,#b8a697,#e4ddd6)"></div>
    <div>
      <h3>Neque porro quisquam est qui dolorem ipsum</h3>
      <div class="meta"><strong>$95</strong><div class="bar"><span></span></div><span>&#9201; Time left: 6 days</span></div>
      <p>Ut enim ad minima veniam, quis nostrum exercitationem ullam corporis suscipit laboriosam, nisi ut aliquid ex ea commodi consequatur quis autem vel eum iure reprehenderit qui in ea voluptate velit.</p>
      <div class="more">READ MORE &rsaquo;</div>
    </div>
  </article>

  <article class="project">
    <div class="thumb" role="img" aria-label="Photo of hands typing on a laptop" style="background:linear-gradient(135deg,#3d3f44,#8b8e93)"></div>
    <div>
      <h3>Neque porro quisquam est qui dolorem ipsum</h3>
      <div class="meta"><strong>$75</strong><div class="bar"><span></span></div><span>&#9201; Time left: 2 days</span></div>
      <p>Quis autem vel eum iure reprehenderit qui in ea voluptate velit esse quam nihil molestiae consequatur, vel illum qui dolorem eum fugiat quo voluptas nulla pariatur at vero eos et accusamus.</p>
      <div class="more">READ MORE &rsaquo;</div>
    </div>
  </article>

  <article class="project">
    <div class="thumb" role="img" aria-label="Photo of a team meeting around a table" style="background:linear-gradient(135deg,#a7b7a4,#dfe3da)"></div>
    <div>
      <h3>Morbi in ante arcu. Maecenas sit amet sem vel</h3>
      <div class="meta"><strong>$120</strong><div class="bar"><span></span></div><span>&#9201; Time left: 5 days</span></div>
      <p>Nam libero tempore, cum soluta nobis est eligendi optio cumque nihil impedit quo minus id quod maxime placeat facere possimus, omnis voluptas assumenda est, omnis dolor repellendus temporibus.</p>
      <div class="more">READ MORE &rsaquo;</div>
    </div>
  </article>

  <article class="project">
    <div class="thumb" role="img" aria-label="Photo of a woman working on a computer" style="background:linear-gradient(135deg,#c7b3a6,#eee7e2)"></div>
    <div>
      <h3>Neque porro quisquam est qui dolorem ipsum</h3>
      <div class="meta"><strong>$60</strong><div class="bar"><span></span></div><span>&#9201; Time left: 3 days</span></div>
      <p>Temporibus autem quibusdam et aut officiis debitis aut rerum necessitatibus saepe eveniet ut et voluptates repudiandae sint et molestiae non recusandae itaque earum rerum hic tenetur sapiente.</p>
      <div class="more">READ MORE &rsaquo;</div>
    </div>
  </article>
</main>

<section class="testimonials">
  <svg width="1200" height="410" viewBox="0 0 1200 410">
    <defs><linearGradient id="warm" x1="0" y1="0" x2="0" y2="1"><stop offset="0" stop-color="#fbab3c"/><stop offset="1" stop-color="#ef7a12"/></linearGradient></defs>
    <path d="M0 70 C300 0 800 0 1200 60 L1200 410 L0 410 Z" fill="url(#warm)"/>
  </svg>
  <div class="testi-copy">
    <h2>CLIENT TESTIMONIALS</h2>
    <p>&ldquo;Working with a whole team of experts at once changed how we approach every launch. Our presentation was sharper, the feedback came fast, and the final result was far better than anything we could have built alone. We will be back with our next project very soon.&rdquo;</p>
    <div class="avatar" role="img" aria-label="Client portrait"></div>
    <p class="name">Lena Marsh</p>
    <p class="role">Marketing Lead</p>
  </div>
  <span class="arrow" style="left:150px">&lsaquo;</span>
  <span class="arrow" style="left:1030px">&rsaquo;</span>
</section>

<section class="clients">
  <span class="client"><i></i>Sonora</span>
  <span class="client"><i></i>Quadrel</span>
  <span class="client">Lumigram</span>
  <span class="client">stockhaven</span>
  <span class="client"><i></i>Cubix</span>
  <span class="client"><i></i>Sonora</span>
</section>

<footer class="site-footer">
  <nav class="foot-nav"><span>HOME</span><span>PROJECTS</span><span>HOW IT WORKS</span><span>PRICING</span><span>MY ACCOUNT</span></nav>
  <p class="copyright">&copy; 2015 Pelmora.com. All rights reserved.</p>
  <div class="social"><i></i><i></i><i></i><i></i><i></i></div>
</footer>

</body>
</html>
```